business card

Business card for new business.
Red and black corporate colors.
Card can have an Indsutrial feel to it. Feel free to add Rust, Bolted steel, or graphics as you see fit. We provide highly specialized services to the below mentioned industries.
Keep information out of corners so that if I want I can choose rounded corners.
Information
- front. name - title - phone - email
- Rear
Refining - Rail - Infrastructure - Mining - Energy
Ashvale - Ridgeford - Fort Calloway - Pinecrest - Northbay

```html
<!DOCTYPE html>
<html lang="en">
<head>
<meta charset="UTF-8">
<title>Girderline Business Card</title>
<link href="https://fonts.googleapis.com/css2?family=Work+Sans:wght@400;500;700&display=swap" rel="stylesheet">
<style>
  :root {
    --backdrop: #2b2b2b;
    --card: #1d1d1d;
    --card-light: #262626;
    --ink: #f2f2f2;
    --ink-soft: #d9d9d9;
    --signal-red: #e8232a;
  }
  * { box-sizing: border-box; margin: 0; padding: 0; }
  html, body {
    width: 1200px;
    height: 900px;
    overflow: hidden;
    background: var(--backdrop);
    font-family: "Work Sans", Arial, sans-serif;
    color: var(--ink);
  }
  .canvas {
    position: relative;
    width: 1200px;
    height: 900px;
  }
  .card {
    position: absolute;
    left: 250px;
    width: 700px;
    height: 400px;
    background: linear-gradient(135deg, var(--card) 0%, var(--card) 55%, var(--card-light) 100%);
  }
  .card--back { top: 40px; }
  .card--front { top: 460px; }

  /* Back side */
  .back-wordmark {
    position: absolute;
    top: 110px;
    left: 0;
    width: 100%;
    text-align: center;
    font-size: 64px;
    font-weight: 700;
    letter-spacing: 2px;
    color: var(--ink-soft);
  }
  .back-lines {
    position: absolute;
    top: 270px;
    left: 0;
    width: 100%;
    text-align: center;
    font-size: 18px;
    line-height: 27px;
    color: var(--ink);
  }

  /* Front side */
  .front-brand {
    position: absolute;
    top: 172px;
    left: 60px;
    display: flex;
    align-items: center;
    gap: 12px;
  }
  .front-brand__square {
    width: 22px;
    height: 22px;
    background: var(--signal-red);
  }
  .front-brand__name {
    font-size: 42px;
    font-weight: 700;
    color: var(--ink);
    letter-spacing: 1px;
  }
  .front-divider {
    position: absolute;
    top: 90px;
    left: 380px;
    width: 2px;
    height: 220px;
    background: var(--ink-soft);
  }
  .contact {
    position: absolute;
    top: 80px;
    left: 420px;
  }
  .contact__name {
    font-size: 27px;
    font-weight: 500;
    color: var(--signal-red);
    letter-spacing: 0.5px;
  }
  .contact__title {
    font-size: 19px;
    margin-bottom: 16px;
  }
  .contact__address {
    font-size: 19px;
    line-height: 25px;
    margin-bottom: 8px;
  }
  .contact__row {
    display: flex;
    align-items: center;
    gap: 12px;
    font-size: 19px;
    line-height: 28px;
  }
  .contact__icon { width: 12px; height: 12px; flex: none; }
  .contact__web-accent { color: var(--signal-red); }
</style>
</head>
<body>
<main class="canvas">

  <section class="card card--back" aria-label="Card back">
    <div class="back-wordmark">GIRDERLINE</div>
    <div class="back-lines">
      <p>Refining - Rail - Infrastructure - Mining - Energy</p>
      <p>Ashvale - Ridgeford - Fort Calloway - Pinecrest - Northbay</p>
    </div>
  </section>

  <section class="card card--front" aria-label="Card front">
    <div class="front-brand">
      <span class="front-brand__square"></span>
      <span class="front-brand__name">GIRDERLINE</span>
    </div>

    <div class="front-divider"></div>

    <div class="contact">
      <p class="contact__name">DANIEL HARROW</p>
      <p class="contact__title">Director</p>
      <p class="contact__address">1270 Ironwood Ave.<br>Dallas, TX 75201</p>

      <p class="contact__row">
        <svg class="contact__icon" viewBox="0 0 12 12" aria-hidden="true">
          <path d="M2 1 L4.5 1 L5.2 3.6 L3.8 4.6 C4.5 6.2 5.8 7.5 7.4 8.2 L8.4 6.8 L11 7.5 L11 10 C6 10.5 1.5 6 2 1 Z" fill="var(--signal-red)"/>
        </svg>
        +330 5182-4406
      </p>
      <p class="contact__row">
        <svg class="contact__icon" viewBox="0 0 12 12" aria-hidden="true">
          <rect x="1" y="2.5" width="10" height="7" fill="none" stroke="var(--signal-red)" stroke-width="1.2"/>
          <path d="M1 2.5 L6 6.5 L11 2.5" fill="none" stroke="var(--signal-red)" stroke-width="1.2"/>
        </svg>
        info@girderline.com
      </p>
      <p class="contact__row">
        <svg class="contact__icon" viewBox="0 0 12 12" aria-hidden="true">
          <circle cx="6" cy="6" r="5" fill="none" stroke="var(--signal-red)" stroke-width="1.1"/>
          <ellipse cx="6" cy="6" rx="2.2" ry="5" fill="none" stroke="var(--signal-red)" stroke-width="1"/>
          <line x1="1" y1="6" x2="11" y2="6" stroke="var(--signal-red)" stroke-width="1"/>
        </svg>
        <span>www.<span class="contact__web-accent">girderline</span>.com</span>
      </p>
    </div>
  </section>

</main>
</body>
</html>
```